cafe marlowpin breakfast lunch dinner menu

I am launching my new menu on the 1st of feb and i need a new menu design asap.

This is our logo that we want on the front page

our cafe is industral rustic however we have trees inside everything is timber inside. quite allot of green plants flowers everyhwere.

these photos should give you a understanding of what my cafe looks like and offers
Thanks

Target Market(s)

cafe

Industry/Entity Type

Cafe

Font styles to use
Sans Serif

Colors
85cae6
000000
ffffff
abd036

Requirements
Must have
• 2 pictures of food
Nice to have
• facebook instgram logo on the bottom so people can know we are on these platforms.

```html
<!DOCTYPE html>
<html lang="en">
<head>
<meta charset="utf-8">
<title>Cafe Marlowpin Menu</title>
<link rel="stylesheet" href="https://fonts.googleapis.com/css2?family=Patua+One&family=Patrick+Hand&display=swap">
<style>
  :root {
    --backdrop: #c9c9c9;
    --chalk: #2a2a2a;
    --chalk-light: #3a3a3a;
    --white: #ffffff;
    --black: #000000;
    --ink: #1c1c1c;
    --sky: #85cae6;
    --leaf: #abd036;
  }
  * { box-sizing: border-box; margin: 0; padding: 0; }
  html, body { width: 1200px; height: 2290px; overflow: hidden; background: var(--backdrop); }
  .canvas {
    width: 1200px; height: 2290px; position: relative;
    font-family: "Patrick Hand", sans-serif; color: var(--white);
  }

  /* Front cover */
  .cover {
    position: absolute; left: 350px; top: 60px; width: 500px; height: 706px;
    overflow: hidden;
  }
  .cover-photo {
    position: absolute; inset: 0;
    background:
      radial-gradient(ellipse 55% 40% at 50% 42%, #d9d9d9 0%, #9a9a9a 45%, transparent 75%),
      linear-gradient(160deg, #4a4a4a 0%, #1e1e1e 45%, #3c3c3c 70%, #141414 100%);
  }
  .cover-logo {
    position: absolute; left: 230px; top: 120px; width: 160px; height: 160px;
    border-radius: 50%; background: var(--white);
    display: flex; flex-direction: column; align-items: center; justify-content: center;
    color: var(--ink); font-size: 30px; line-height: 1; text-align: center;
  }

  /* Inside spread */
  .spread {
    position: absolute; left: 170px; top: 841px; width: 860px; height: 607px;
    display: flex;
  }
  .page {
    width: 430px; height: 607px; position: relative;
    background: linear-gradient(180deg, var(--chalk-light) 0%, var(--chalk) 60%, #242424 100%);
  }
  .page + .page { border-left: 1px solid #1a1a1a; }
  .photo-row { display: flex; height: 100px; }
  .food-photo { flex: 1; height: 100%; }
  .food-photo.sandwich { background: linear-gradient(135deg, #6b4a2a, #b08a4a 50%, #4f3a22); }
  .food-photo.wrap { background: linear-gradient(135deg, #5d6a7a, #a9a28a 50%, #4a5a3a); }
  .food-photo.waffles { background: linear-gradient(135deg, #3a2418, #7a4a2a 50%, #c9b9a8); }
  .food-photo.pancakes { background: linear-gradient(135deg, #8a6a5a, #c98a6a 50%, #e9c9b9); }

  .menu-columns {
    position: absolute; left: 0; right: 0; top: 100px; bottom: 0;
    display: flex; padding: 22px 14px 0;
  }
  .menu-column { flex: 1; display: flex; flex-direction: column; align-items: center; gap: 16px; }
  .column-rule { width: 3px; background: var(--white); margin: 0 8px; height: 262px; border-radius: 2px; }
  .menu-item { text-align: center; width: 100%; }
  .item-name {
    display: inline-block; background: var(--white); color: var(--ink);
    font-family: "Patua One", sans-serif; font-size: 16px;
    padding: 3px 14px 4px; margin-bottom: 8px; min-width: 124px;
  }
  .item-note, .item-desc { font-size: 12.5px; line-height: 1.2; }
  .item-price { font-size: 22px; margin-top: 3px; line-height: 1.1; }

  /* Back cover */
  .back {
    position: absolute; left: 350px; top: 1523px; width: 500px; height: 706px;
    overflow: hidden; background: var(--chalk);
  }
  .interior-photos {
    position: absolute; left: 0; top: 0; width: 500px; height: 470px;
    background:
      linear-gradient(100deg, #7a3a3a 0%, #5a4a3a 20%, #8a6a48 45%, #4a4a4a 65%, #9a7a58 85%, #6a5a4a 100%);
  }
  .back-band {
    position: absolute; left: 0; top: 470px; right: 0; bottom: 0;
    display: flex; flex-direction: column; align-items: center; padding-top: 34px;
    background: linear-gradient(180deg, var(--chalk-light), var(--chalk));
  }
  .back-logo {
    width: 100px; height: 100px; border-radius: 50%; background: var(--white);
    display: flex; flex-direction: column; align-items: center; justify-content: center;
    color: var(--ink); font-size: 19px; line-height: 1; text-align: center;
  }
  .social { display: flex; gap: 10px; margin-top: 34px; }
  .social-dot { width: 26px; height: 26px; border-radius: 50%; background: var(--white); }
</style>
</head>
<body>
<div class="canvas">

  <section class="cover">
    <div class="cover-photo" role="img" aria-label="Cafe storefront photo with a large white tree illustration"></div>
    <div class="cover-logo"><span>Cafe</span><span>Marlowpin</span></div>
  </section>

  <section class="spread">
    <article class="page">
      <div class="photo-row">
        <div class="food-photo sandwich" role="img" aria-label="Photo of a toasted sandwich"></div>
        <div class="food-photo wrap" role="img" aria-label="Photo of a loaded wrap"></div>
        <div class="food-photo waffles" role="img" aria-label="Photo of stacked waffles with ice cream"></div>
      </div>
      <div class="menu-columns">
        <div class="menu-column">
          <div class="menu-item">
            <div class="item-name">El Narco</div>
            <p class="item-desc">6oz Chuck Steak Patty<br>Monterey Jack - Homemade Salsa<br>Mac Daddy Sauce - Red Onion<br>Rocket - Beef Heart Tomato -<br>Crushed Corn Tortilla</p>
            <p class="item-price">£7.50</p>
          </div>
          <div class="menu-item">
            <div class="item-name">Fairway Fries (v)</div>
            <p class="item-desc">Skin On Fries - Secret Seasoning<br>Fresh Chillies - Melted Cheese</p>
            <p class="item-price">£3.50</p>
          </div>
          <div class="menu-item">
            <div class="item-name">Nachos Royale</div>
            <p class="item-desc">Corn Tortillas<br>Homemade Salsa - Melted Cheese<br>Chopped Green &amp; Red Chillies</p>
          </div>
        </div>
        <div class="column-rule"></div>
        <div class="menu-column">
          <div class="menu-item">
            <div class="item-name">The Fabulous</div>
            <p class="item-desc">Monterey Jack - Beef Heart Tomato<br>Mac Daddy Sauce - Dill Pickles<br>Red Onions - Rocket</p>
            <p class="item-price">£6</p>
          </div>
          <div class="menu-item">
            <div class="item-name">Proper Manc</div>
            <p class="item-note">(we love our city)</p>
            <p class="item-desc">Monterey Jack - Beef Heart Tomato<br>Manc Sauce - Dill Pickles<br>Red Onions - Rocket</p>
            <p class="item-price">£6</p>
          </div>
          <div class="menu-item">
            <div class="item-name">Junkyard Dog</div>
            <p class="item-note">(Kosher &amp; Halal)</p>
            <p class="item-desc">1/4lb 100% Beef Frankfurter<br>Dill Pickles - Ketchup - Brantley's Mustard<br>Served On A New York Sub</p>
          </div>
        </div>
      </div>
    </article>

    <article class="page">
      <div class="photo-row">
        <div class="food-photo waffles" role="img" aria-label="Photo of waffles topped with ice cream"></div>
        <div class="food-photo pancakes" role="img" aria-label="Photo of a breakfast plate"></div>
        <div class="food-photo waffles" role="img" aria-label="Photo of stacked waffles with a drink"></div>
      </div>
      <div class="menu-columns">
        <div class="menu-column">
          <div class="menu-item">
            <div class="item-name">El Narco</div>
            <p class="item-desc">6oz Chuck Steak Patty<br>Monterey Jack - Homemade Salsa<br>Mac Daddy Sauce - Red Onion<br>Rocket - Beef Heart Tomato -<br>Crushed Corn Tortilla</p>
            <p class="item-price">£7.50</p>
          </div>
          <div class="menu-item">
            <div class="item-name">Fairway Fries (v)</div>
            <p class="item-desc">Skin On Fries - Secret Seasoning<br>Fresh Chillies - Melted Cheese</p>
            <p class="item-price">£3.50</p>
          </div>
          <div class="menu-item">
            <div class="item-name">Nachos Royale</div>
            <p class="item-desc">Corn Tortillas<br>Homemade Salsa - Melted Cheese<br>Chopped Green &amp; Red Chillies</p>
          </div>
        </div>
        <div class="column-rule"></div>
        <div class="menu-column">
          <div class="menu-item">
            <div class="item-name">The Fabulous</div>
            <p class="item-desc">Monterey Jack - Beef Heart Tomato<br>Mac Daddy Sauce - Dill Pickles<br>Red Onions - Rocket</p>
            <p class="item-price">£6</p>
          </div>
          <div class="menu-item">
            <div class="item-name">Proper Manc</div>
            <p class="item-note">(we love our city)</p>
            <p class="item-desc">Monterey Jack - Beef Heart Tomato<br>Manc Sauce - Dill Pickles<br>Red Onions - Rocket</p>
            <p class="item-price">£6</p>
          </div>
          <div class="menu-item">
            <div class="item-name">Junkyard Dog</div>
            <p class="item-note">(Kosher &amp; Halal)</p>
            <p class="item-desc">1/4lb 100% Beef Frankfurter<br>Dill Pickles - Ketchup - Brantley's Mustard<br>Served On A New York Sub</p>
          </div>
        </div>
      </div>
    </article>
  </section>

  <section class="back">
    <div class="interior-photos" role="img" aria-label="Collage of cafe interior photos: leather sofa, timber tables, tree trunk décor and the counter"></div>
    <div class="back-band">
      <div class="back-logo"><span>Cafe</span><span>Marlowpin</span></div>
      <div class="social">
        <span class="social-dot"></span>
        <span class="social-dot"></span>
      </div>
    </div>
  </section>

</div>
</body>
</html>
```